Book Cover for Fitness Trainer for Men

My name is Daisy Mae Corwin. I am a female Fitness Trainer for Men.
I need a new Book Cover Design for my second book and a back of the book.
Both with updated text.
#A… Book Cover… I like the bright red and yellow colors.
I like the weight rack and the bold headline Font
#B… Book Cover…I like the full frontal sexier body. I don not like the font style.
I want the new design sexier; super sexy. Even more eye catching for guys.
I want to push the envelope to the point of almost too much sexy.
An Brindle book 6”x9”, 150 pages

Target Market(s)

Men

Industry/Entity Type

Health and fitness for men

Colors
FFF300
FFF600
FEFA6F
FFFEC7
FFFEE8
EB3D1F
EC4F4E
F09395
F8D3D4
FCEDEE

Requirements
Must have
• Sexy & eye catching.

```html
<!DOCTYPE html>
<html lang="en">
<head>
<meta charset="utf-8">
<title>Pushing Guys Get Lean, Strong &amp; Fit – Volume II</title>
<link rel="stylesheet" href="https://fonts.googleapis.com/css2?family=Bebas+Neue&family=Montserrat:wght@400;500;600;700;800&display=swap">
<style>
  :root {
    --stage: #e3e3e1;
    --red: #f71b1a;
    --yellow: #fff300;
    --white: #ffffff;
    --skin-light: #e9b79a;
    --skin-dark: #b97559;
    --plate: #0f0f0f;
  }
  * { box-sizing: border-box; margin: 0; padding: 0; }
  html, body { width: 854px; height: 1200px; overflow: hidden; }
  body { background: var(--stage); font-family: "Montserrat", sans-serif; position: relative; }

  .cover-spread {
    position: absolute; left: 20px; top: 319px;
    width: 814px; height: 562px;
    background: var(--red); overflow: hidden; color: var(--white);
  }

  /* ---------- back cover ---------- */
  .back-copy {
    position: absolute; left: 29px; top: 31px; width: 323px;
    font-size: 7.6px; line-height: 9.4px; text-align: justify;
  }
  .back-copy p { margin-bottom: 9px; }
  .back-copy .highlight { color: var(--yellow); font-weight: 600; text-align: left; }
  .back-copy strong { font-weight: 700; }
  .back-copy .section-title { font-weight: 600; margin-top: 14px; margin-bottom: 5px; text-align: left; }
  .back-copy .closing { margin-top: 14px; }
  .back-copy .mission { font-size: 8.4px; line-height: 10.4px; text-align: left; }

  .author-portrait {
    position: absolute; left: 29px; top: 430px; width: 85px; height: 94px;
    border: 3px solid var(--white);
    background: linear-gradient(160deg, #d9c3ad 0%, #b88a68 55%, #5b6f6a 100%);
  }
  .author-name {
    position: absolute; left: 123px; top: 490px;
    color: var(--yellow); font-weight: 700; font-size: 13px; line-height: 1;
  }
  .author-role { position: absolute; left: 123px; top: 506px; font-size: 7px; }
  .back-cta {
    position: absolute; left: 29px; top: 523px;
    font-size: 9.2px; font-weight: 600; white-space: nowrap;
  }

  /* ---------- spine ---------- */
  .spine-title {
    position: absolute; top: 34px; left: 385px;
    writing-mode: vertical-rl;
    font-family: "Bebas Neue", sans-serif; font-weight: 400;
    font-size: 27px; line-height: 24px;
  }
  .spine-title .accent { color: var(--yellow); }
  .spine-volume {
    position: absolute; top: 278px; left: 401px;
    writing-mode: vertical-rl; font-weight: 700; font-size: 10.5px; letter-spacing: 0.5px;
  }
  .spine-author {
    position: absolute; top: 384px; left: 396px;
    writing-mode: vertical-rl; line-height: 1;
  }
  .spine-author .name { font-weight: 800; font-size: 13.5px; }
  .spine-author .role { font-size: 6px; letter-spacing: 2.2px; margin-left: 5px; }

  /* ---------- front cover ---------- */
  .weight-plate {
    position: absolute; left: 378px; top: 381px; width: 290px; height: 290px;
    border-radius: 50%; background: var(--plate);
  }
  .model-photo {
    position: absolute; left: 615px; top: 0; width: 199px; height: 562px;
    background: linear-gradient(90deg, var(--skin-dark) 0%, var(--skin-light) 45%, #d69c7e 75%, var(--skin-dark) 100%);
  }
  .front-author { position: absolute; left: 451px; top: 31px; }
  .front-author .name { font-weight: 800; font-size: 21px; line-height: 1; letter-spacing: 0.2px; }
  .front-author .role { font-weight: 600; font-size: 9px; letter-spacing: 3.6px; margin-top: 6px; }

  .headline {
    position: absolute; left: 451px; top: 135px;
    font-family: "Bebas Neue", sans-serif; font-weight: 400;
    text-transform: uppercase;
  }
  .headline span { display: block; line-height: 0.86; }
  .headline .lead { font-size: 48px; }
  .headline .big { font-size: 74px; }
  .headline .accent { color: var(--yellow); }

  .tagline {
    position: absolute; left: 452px; top: 413px;
    border-left: 2px solid var(--white); padding: 7px 0 6px 7px;
    font-weight: 700; font-size: 12.5px; line-height: 18px; text-transform: uppercase;
  }
  .front-volume {
    position: absolute; left: 453px; top: 520px;
    font-weight: 700; font-size: 18px; line-height: 1;
  }
</style>
</head>
<body>
  <main class="cover-spread">
    <section class="back-cover">
      <div class="back-copy">
        <p>I’ve always used a little eye candy to pull guys into health and fitness. From my first day on the gym floor, heads turned and I noticed. If a hot trainer gets you off the couch, I’m happy to be that trainer. It pays the bills and gets my guys healthier. Years of coaching Men taught me one thing...no two Guys are built alike. Every one of you is different, and You have to find what fits You. Once you do... the weight drops off, your belly flattens, and your health takes off.</p>
        <p>You’ll love the new you. Your girlfriend will notice. Your wife will notice.<br><span class="highlight">Nothing turns a woman on like a strong, fit man with stamina.</span></p>
        <p>Everyone in the fitness world keeps shouting about pricey gym plans, 30day challenges, and total diet overhauls ... My Guys skip all of it. My Guys are Real Men with Real bodies. Real Men with jobs, families, and no spare hours to spend in a gym.</p>
        <p>Real men are sick of show-off gym rats, their 1% body fat and abs nobody else will ever have. Those guys are full of it! And they’ll be the first ones reading my book. Ya gotta love it.</p>
        <p class="section-title">FIND WHAT WORKS FOR YOU.</p>
        <p>“I tweaked a few meals, added a little exercise and dropped 17 pounds in three months. Thanks Daisy. Couldn’t have done it without you.”</p>
        <p>“Daisy! I took the bait and it all made sense. Can’t believe you got me moving. My gut shrank and I had to buy new jeans. Best 20 bucks I ever spent.” “<strong>I’ve paid for pricey</strong> 30day plans but your <strong>Ultimate Workout</strong> was all I ever needed. You’re right, <strong>No damn</strong> secret at all.” “<strong>Smart eating with Fast food</strong> is brilliant. Never thought I could keep eating “the good stuff” and still slim down. WOW!” “<strong>My climbing weight</strong> was scaring me half to death. You showed me the small changes I can handle...and they changed everything.” “Everyone told me to flip my whole life upside down. I just can’t. All these small “Tricks of the Trade” I can handle.” Thank you Daisy.”</p>
        <p class="highlight closing">Real Men can be fit, strong and healthy whatever their size, weight, or body fat.</p>
        <p class="mission">My goal is to get your lazy butt in shape by finding what works for you. If I have to grab your attention first...Then that’s exactly what I’ll do.</p>
      </div>
      <div class="author-portrait" role="img" aria-label="Portrait photo of the author"></div>
      <p class="author-name">Daisy Mae Corwin</p>
      <p class="author-role">Fitness Trainer for Men</p>
      <p class="back-cta">Think twenty bucks can get You Lean, Strong, and Fit? Try me.</p>
    </section>

    <section class="spine">
      <h2 class="spine-title">PUSHING GUYS GET LEAN,<br><span class="accent">STRONG, &amp; FIT</span></h2>
      <p class="spine-volume">VOLUME II</p>
    </section>

    <section class="front-cover">
      <div class="weight-plate" role="img" aria-label="Black barbell weight plate"></div>
      <div class="spine-author">
        <span class="name">DAISY MAE CORWIN</span><br><span class="role">FITNESS TRAINER FOR MEN</span>
      </div>
      <div class="model-photo" role="img" aria-label="Photo of a fit female model in a black bikini"></div>
      <div class="front-author">
        <p class="name">DAISY MAE CORWIN</p>
        <p class="role">FITNESS TRAINER FOR MEN</p>
      </div>
      <h1 class="headline">
        <span class="lead">Pushing Guys</span>
        <span class="big">Get Lean</span>
        <span class="big accent">Strong</span>
        <span class="big accent">&amp; Fit</span>
      </h1>
      <p class="tagline">So the fat burns off,<br>your belly flattens,<br>&amp; you go all night.</p>
      <p class="front-volume">VOLUME II</p>
    </section>
  </main>
</body>
</html>
```